Update patient consent forms and contract

Objective
Redesign the existing patient contract information document to create a modern,contempory, and easy-to-understand experience for patients. The updated design should improve readability, accessibility, and overall presentation while maintaining compliance with healthcare and legal requirements.

Key Deliverables

Refreshed visual design and layout
Improved information hierarchy and readability
Modern typography and colour palette aligned with brand guidelines
Clear section headings and navigation
Print-ready and digital versions (PDF)

Include KEV Logo within patient KEV consent to treatment. Ideally this document should be portrait not landscape.
Updates

I would love a front page to be included in the document

```html
<!DOCTYPE html>
<html lang="en">
<head>
<meta charset="utf-8">
<title>Payment Option Selection</title>
<link href="https://fonts.googleapis.com/css2?family=Outfit:wght@400;500;600;700&family=Roboto:wght@500&display=swap" rel="stylesheet">
<style>
:root{
  --navy:#1f3356;
  --ink:#2a2a2a;
  --brand:#0098d8;
  --band:#d3effc;
  --line:#7fc9ee;
  --foot-grey:#ececec;
  --stage:#b5b5b5;
  --paper:#ffffff;
  --muted:#8a8a8a;
}
*{box-sizing:border-box;margin:0;padding:0}
html,body{width:1200px;height:943px;overflow:hidden;background:var(--stage);font-family:"Outfit",sans-serif;color:var(--ink)}
.sheet{position:absolute;left:255px;top:25px;width:690px;height:893px;background:var(--paper)}
.abs{position:absolute}
.title{left:37px;top:30px;font-size:25px;font-weight:700;color:var(--navy);letter-spacing:-.2px}
.partner{left:365px;top:38px;display:flex;align-items:center;gap:6px;font-size:16px;font-weight:600;color:var(--muted)}
.partner .dot{width:14px;height:14px;border-radius:50%;background:var(--muted)}
.brand{left:522px;top:38px;display:flex;align-items:center;gap:6px;font-size:16px;font-weight:600;color:var(--brand)}
.brand .sq{width:14px;height:14px;background:var(--brand)}
.thanks{left:40px;top:79px;font-size:12.5px;font-weight:700}
.intro{left:40px;top:108px;width:620px;font-size:12.3px;line-height:20px}
.section-head{left:25px;font-size:19px;font-weight:600;color:var(--brand);display:flex;align-items:center;gap:8px}
.section-head::before{content:"";width:4px;height:4px;border-radius:50%;background:var(--brand)}
.band{left:0;top:222px;width:690px;height:274px;background:var(--band)}
.check{left:45px;width:21px;height:21px;background:#fff;border:1.3px solid var(--line);border-radius:3px}
.opt-title{left:76px;font-family:"Roboto",sans-serif;font-weight:500;font-size:13px;color:var(--navy)}
.opt-text{left:40px;width:610px;font-size:12px;line-height:16px}
.divider{left:45px;top:362px;width:602px;border-top:1px dashed #fff}
.body{left:40px;width:590px;font-size:12px;line-height:16px}
.sign-line{top:727px;width:116px;border-top:1px solid var(--ink)}
.sign-label{top:735px;width:116px;text-align:center;font-size:13px;font-weight:600}
.footer{left:0;top:772px;width:690px;height:121px;background:var(--foot-grey)}
.bank{left:0;top:772px;width:222px;height:121px;background:var(--brand);color:#fff;padding:14px 0 0 40px;font-size:8.5px}
.bank h3,.info h3,.team h3{font-size:9.5px;font-weight:600;margin-bottom:7px}
.bank dl{display:grid;grid-template-columns:92px 1fr;row-gap:9px}
.bank dd{font-weight:600}
.info{left:222px;top:772px;width:225px;padding:14px 0 0 22px;font-size:8.5px;color:var(--ink)}
.info li{list-style:none;display:flex;align-items:center;gap:7px;margin-bottom:7px}
.info svg{width:11px;height:11px;flex:none}
.sep{left:447px;top:787px;height:88px;border-left:1px solid #fff}
.team{left:471px;top:772px;padding-top:14px;font-size:8px;color:var(--ink)}
.team li{list-style:none;display:flex;gap:6px;margin-bottom:6px;line-height:10px}
.team svg{width:12px;height:14px;flex:none;margin-top:2px}
.team strong{font-weight:700;font-size:8.5px;display:block}
</style>
</head>
<body>
<main class="sheet">
  <h1 class="abs title">Payment Option Selection</h1>
  <div class="abs partner"><span class="dot"></span>KEV</div>
  <div class="abs brand"><span class="sq"></span>Lumen Orthodontics</div>

  <p class="abs thanks">Thank you for choosing Lumen Orthodontics.</p>
  <p class="abs intro">To assist with managing your treatment fees, please select your preferred payment method below. If you would prefer to pay at each scheduled appointment, please advise our reception team. Please note that appointments are generally scheduled every 6–8 weeks.</p>

  <h2 class="abs section-head" style="top:195px">Please select one option:</h2>

  <div class="abs band"></div>

  <span class="abs check" style="top:234px"></span>
  <h3 class="abs opt-title" style="top:236px">Credit Card Direct Debit</h3>
  <svg class="abs" style="left:333px;top:243px" width="58" height="42" viewBox="0 0 58 42" fill="none" stroke="var(--line)" stroke-width="1.5">
    <rect x="1" y="1" width="46" height="31" rx="2"/>
    <line x1="1" y1="19" x2="47" y2="19"/><line x1="1" y1="23" x2="47" y2="23"/>
    <line x1="7" y1="8" x2="23" y2="8"/><line x1="7" y1="12" x2="15" y2="12"/>
    <circle cx="46" cy="31" r="9" fill="var(--band)"/>
    <path d="M41 31h9M46.5 27.5 50 31l-3.5 3.5"/>
  </svg>
  <p class="abs opt-text" style="top:266px">I would like to pay via credit card direct debit.</p>
  <p class="abs opt-text" style="top:297px">I understand that Lumen Orthodontics will send me a secure PayLink payment link to enter my credit card details. The card provided will be securely stored and used as my nominated payment method for future scheduled payments relating to my treatment plan.</p>

  <div class="abs divider"></div>

  <span class="abs check" style="top:380px"></span>
  <h3 class="abs opt-title" style="top:382px">Monthly Direct Bank Transfer</h3>
  <svg class="abs" style="left:333px;top:381px" width="46" height="42" viewBox="0 0 46 42" fill="none" stroke="var(--line)" stroke-width="1.5">
    <rect x="1" y="5" width="43" height="35" rx="4"/>
    <line x1="1" y1="14" x2="44" y2="14"/>
    <line x1="12" y1="1" x2="12" y2="9"/><line x1="33" y1="1" x2="33" y2="9"/>
    <path d="M13 23h19l-4-3M32 30H13l4 3"/>
  </svg>
  <p class="abs opt-text" style="top:411px">I would like to pay via monthly direct bank transfer.</p>
  <p class="abs opt-text" style="top:442px">I understand that I am responsible for ensuring monthly payments are made on time in accordance with my agreed payment arrangement.</p>

  <h2 class="abs section-head" style="top:513px">Important</h2>
  <p class="abs body" style="top:539px">When making direct transfer payments, please use the <strong>patient's full name</strong> as the payment reference (for example: Jane Citizen), rather than the account holder's name. This ensures payments are correctly allocated to your treatment account.</p>

  <h2 class="abs section-head" style="top:604px">Patient Declaration</h2>
  <p class="abs body" style="top:628px;width:620px">I have read and understood the payment options above and agree to my selected payment method.</p>

  <div class="abs sign-line" style="left:107px"></div>
  <span class="abs sign-label" style="left:107px">Signature</span>
  <div class="abs sign-line" style="left:468px"></div>
  <span class="abs sign-label" style="left:468px">Date</span>

  <div class="abs footer"></div>
  <section class="abs bank">
    <h3>Our bank account details:</h3>
    <dl>
      <dt>Account Name</dt><dd>: Lumen Ortho</dd>
      <dt>Bank</dt><dd>: Harbour Bank</dd>
      <dt>BSB</dt><dd>: 000 111</dd>
      <dt>Account Number</dt><dd>: 12345678</dd>
    </dl>
  </section>
  <section class="abs info">
    <h3>Information:</h3>
    <ul>
      <li><svg viewBox="0 0 12 12" fill="none" stroke="var(--brand)"><path d="M6 11S2 7 2 4.5a4 4 0 0 1 8 0C10 7 6 11 6 11z"/><circle cx="6" cy="4.5" r="1.4"/></svg>48 Ridgeway Rd, Hillcrest VIC 3999</li>
      <li><svg viewBox="0 0 12 12" fill="none" stroke="var(--brand)"><path d="M2 1.5h2.5l1 2.5-1.5 1a6 6 0 0 0 3 3l1-1.5 2.5 1V10A1 1 0 0 1 9.5 11 8.5 8.5 0 0 1 1 2.5a1 1 0 0 1 1-1z"/></svg>03 9000 1234</li>
      <li><svg viewBox="0 0 12 12" fill="none" stroke="var(--brand)"><rect x="1.5" y="4" width="9" height="6.5"/><rect x="3.5" y="1.5" width="5" height="2.5"/><line x1="3.5" y1="7" x2="8.5" y2="7"/></svg>03 9000 5678</li>
      <li><svg viewBox="0 0 12 12" fill="none" stroke="var(--brand)"><rect x="1.5" y="2.5" width="9" height="7"/><path d="M1.5 2.5 6 6.5l4.5-4"/></svg>hello@lumen-ortho.example</li>
    </ul>
  </section>
  <div class="abs sep"></div>
  <section class="abs team">
    <h3>Registered Specialist Orthodontists:</h3>
    <ul>
      <li><svg viewBox="0 0 12 14" fill="none" stroke="var(--brand)"><path d="M3 1.5C1 1.5 1 4 1.5 6S2.5 12.5 3.5 12.5 4.5 8 6 8s1.5 4.5 2.5 4.5S10 8 10.5 6 11 1.5 9 1.5 7 2.5 6 2.5 5 1.5 3 1.5z"/></svg><span><strong>Dr Hannah Rowe</strong>MDSc, Grad Dip Clin Dent, BDSc(Hons)</span></li>
      <li><svg viewBox="0 0 12 14" fill="none" stroke="var(--brand)"><path d="M3 1.5C1 1.5 1 4 1.5 6S2.5 12.5 3.5 12.5 4.5 8 6 8s1.5 4.5 2.5 4.5S10 8 10.5 6 11 1.5 9 1.5 7 2.5 6 2.5 5 1.5 3 1.5z"/></svg><span><strong>Dr Peter Lund</strong>MDSc, Grad Dip Clin Dent, MOrth, BDSc</span></li>
      <li><svg viewBox="0 0 12 14" fill="none" stroke="var(--brand)"><path d="M3 1.5C1 1.5 1 4 1.5 6S2.5 12.5 3.5 12.5 4.5 8 6 8s1.5 4.5 2.5 4.5S10 8 10.5 6 11 1.5 9 1.5 7 2.5 6 2.5 5 1.5 3 1.5z"/></svg><span><strong>Dr Marcus Lee</strong>DCD, MOrth, MRACDS (Orth), BDSc (Hons)</span></li>
    </ul>
  </section>
</main>
</body>
</html>
```